Kickbut Home Page Design built to Sell

We need a new home page layout. The website is working now but we need a refresh. Our business has slowed down since a few years ago. We need to show we build ecommerce and membership websites. Here is the page now: https://www.brelvoxstudio.graphics/new-home/

Target Market(s)

Women, solopreneurs, artists, politicians

Industry/Entity Type

Design Agency

Number of Pages Required

1 page

Font styles to use
Sans Serif

Colors
b8a6cd
fabb94
acd136
00a990

Requirements
Must have
• Video header
Section for text and Step process similar to this website: https://quintarelweb.com/ [This is out sister company]
Places for images.
Call to action lead gen form and Get a quote.
The menu should show WEB, PRINT, VIDEO
Nice to have
• I LOVE this company: https://tarnwickly.com/guide/
Area for testimonials
Should not have
• We don't want a duplicate of https://quintarelweb.com/

```html
<!DOCTYPE html>
<html lang="en">
<head>
<meta charset="utf-8">
<title>Brelvox Studio — Lead Generating Websites</title>
<link href="https://fonts.googleapis.com/css2?family=Jost:wght@500;600&family=Roboto:ital,wght@0,400;0,500;0,700;1,400&display=swap" rel="stylesheet">
<style>
:root{
  --purple:#b8a6cd;
  --purple-btn:#b49fd2;
  --purple-icon:#bca8d3;
  --green:#acd136;
  --teal:#00a990;
  --peach:#fabb94;
  --ink:#111111;
  --body:#6d6d6d;
  --white:#ffffff;
  --star:#f6c200;
}
*{margin:0;padding:0;box-sizing:border-box}
html,body{width:1200px;height:2898px;overflow:hidden}
body{position:relative;font-family:'Roboto',sans-serif;color:var(--ink);background:var(--white)}
.abs{position:absolute}
.heading{font-family:'Jost',sans-serif;font-weight:600;text-transform:uppercase}

/* hero */
.hero{left:0;top:0;width:1200px;height:643px;background:linear-gradient(100deg,#5c5346 0%,#7a6d5e 35%,#8d7f70 55%,#a69888 75%,#6f6558 100%)}
.hero-shade{left:0;top:0;width:1200px;height:643px;background:linear-gradient(90deg,rgba(30,25,20,.45),rgba(30,25,20,.05))}
.brand{left:111px;top:22px;color:var(--white)}
.brand-name{font-family:'Jost',sans-serif;font-weight:600;font-size:27px;letter-spacing:.5px;line-height:1}
.brand-tag{font-size:7px;letter-spacing:1.2px;margin-top:3px;font-weight:500}
.nav{top:34px;left:735px;display:flex;gap:28px;color:var(--white);font-weight:700;font-size:14px}
.btn{display:flex;align-items:center;gap:10px;background:var(--purple-btn);color:var(--white);font-weight:700;font-size:14px;text-transform:uppercase;padding:0 16px;border-radius:3px}
.btn-apply{left:953px;top:20px;height:43px}
.hero-title{left:111px;top:242px;width:600px;color:var(--white);font-size:39px;line-height:47px;letter-spacing:.2px}
.hero-sub{left:111px;top:398px;width:560px;color:var(--white);font-weight:700;font-size:16.5px;line-height:26px;text-transform:uppercase}
.play{left:111px;top:468px}

/* process */
.process-photo{left:118px;top:751px;width:459px;height:458px;background:var(--white);box-shadow:0 0 8px rgba(0,0,0,.15);padding:5px}
.process-photo div{width:100%;height:100%;background:linear-gradient(135deg,#e9eef0 0%,#d9c48a 45%,#e3a33a 60%,#c9d6de 100%)}
.process-title{left:658px;top:756px;font-size:35px}
.step{left:658px;width:420px;display:flex;gap:26px}
.step-icon{flex:none;width:60px;height:60px;border-radius:50%;background:var(--purple-icon);display:flex;align-items:center;justify-content:center;margin-top:16px}
.step h3{font-size:14px;font-weight:700;text-transform:uppercase;margin-bottom:8px}
.step p{font-size:14.5px;color:var(--body);line-height:21px}
.btn-quote{left:658px;top:1147px;height:46px}

/* works */
.works-title{left:0;width:1200px;top:1315px;text-align:center;font-size:35px}
.works{left:111px;top:1394px;display:grid;grid-template-columns:repeat(4,236px);grid-auto-rows:177px;gap:13px 11.5px}
.works div{width:236px;height:177px}

/* testimonials */
.clients{left:0;top:1855px;width:1200px;height:448px;background:linear-gradient(180deg,#b7a4cd,#b19dcc)}
.clients-title{left:0;width:1200px;top:1906px;text-align:center;color:var(--white);font-size:35px}
.card{top:2000px;width:320px;height:208px;background:var(--white);overflow:hidden}
.card-flag{left:0;top:0}
.card blockquote{position:absolute;left:29px;top:49px;width:280px;font-style:italic;font-size:14.5px;line-height:23px;color:var(--body)}
.stars{position:absolute;left:29px;top:119px;color:var(--star);font-size:14px;letter-spacing:1px}
.avatar{position:absolute;left:29px;top:149px;width:58px;height:46px;background:linear-gradient(135deg,#d6dadf,#8a8f96)}
.person{position:absolute;left:114px;top:153px;font-size:14px;line-height:18px}
.person strong{display:block;font-weight:500;text-transform:uppercase}
.person span{color:#444;font-weight:500}

/* contact */
.contact{left:0;top:2303px;width:1200px;height:550px;background:var(--green)}
.contact-title{left:0;width:1200px;top:2372px;text-align:center;color:var(--white);font-size:35px}
.contact-lead{left:230px;width:740px;top:2437px;text-align:center;color:var(--white);font-size:14.5px;line-height:22px}
.info{left:107px;display:flex;gap:24px;color:var(--white)}
.info-icon{flex:none;width:50px;height:50px;border-radius:50%;background:var(--white);display:flex;align-items:center;justify-content:center}
.info h4{font-size:14px;font-weight:700;text-transform:uppercase;margin-bottom:8px}
.info p{font-size:14.5px;font-weight:500;line-height:22px}
.info .big{font-size:17px}
.field{left:437px;width:316px;height:49px;background:var(--white);display:flex;align-items:center;justify-content:space-between;padding:0 20px;font-size:14.5px;color:#555}
.field-message{left:777px;top:2520px;width:317px;height:169px;align-items:flex-start;padding-top:17px}
.btn-send{left:777px;top:2703px;height:46px}

.footer{left:0;top:2853px;width:1200px;height:45px;background:var(--purple);color:var(--white);display:flex;align-items:center;justify-content:center;font-weight:500;font-size:15px}
</style>
</head>
<body>

<header>
  <div class="abs hero" role="img" aria-label="Photo of a couple working together on a laptop at home"></div>
  <div class="abs hero-shade"></div>
  <div class="abs brand">
    <div class="brand-name">BRELVOX STUDIO</div>
    <div class="brand-tag">GRAPHICS WEB VIDEO CONSULTANTS</div>
  </div>
  <nav class="abs nav"><span>WEB</span><span>PRINT</span><span>VIDEO</span></nav>
  <a class="abs btn btn-apply">Apply Now
    <svg width="14" height="14" viewBox="0 0 14 14"><circle cx="7" cy="7" r="7" fill="#fff"/><path d="M5 4l3.5 3L5 10" stroke="#b49fd2" stroke-width="2" fill="none"/></svg></a>
  <h1 class="abs heading hero-title">Lead generating websites that move your business forward</h1>
  <p class="abs hero-sub">Your company deserves a website that can inspire people to take action</p>
  <svg class="abs play" width="60" height="60" viewBox="0 0 60 60" aria-label="Play video">
    <circle cx="30" cy="30" r="30" fill="#fff"/><circle cx="30" cy="30" r="21" fill="#b8a6cd"/><path d="M25 21l13 9-13 9z" fill="#fff"/>
  </svg>
</header>

<section>
  <div class="abs process-photo"><div role="img" aria-label="Photo of a smiling woman in a yellow sweater using a laptop"></div></div>
  <h2 class="abs heading process-title">Our Process</h2>

  <div class="abs step" style="top:826px">
    <div class="step-icon"><svg width="34" height="30" viewBox="0 0 34 30" fill="none" stroke="#fff" stroke-width="2"><rect x="2" y="2" width="30" height="20" rx="2"/><path d="M8 9h18M8 14h12M13 27h8M17 22v5"/></svg></div>
    <div><h3>Step&nbsp; 01 &nbsp;-&nbsp;&nbsp; Lorem ipsum dolor sit amet</h3><p>Sed ut perspiciatis unde omnis iste natus error sit voluptatem accusantium doloremque</p></div>
  </div>
  <div class="abs step" style="top:933px">
    <div class="step-icon"><svg width="34" height="30" viewBox="0 0 34 30" fill="none" stroke="#fff" stroke-width="2"><rect x="2" y="2" width="30" height="20" rx="2"/><path d="M11 17l9-9 3 3-9 9h-3z M13 27h8M17 22v5"/></svg></div>
    <div><h3>Step&nbsp; 02 &nbsp;-&nbsp;&nbsp; Lorem ipsum dolor sit amet</h3><p>Sed ut perspiciatis unde omnis iste natus error sit voluptatem accusantium doloremque</p></div>
  </div>
  <div class="abs step" style="top:1040px">
    <div class="step-icon"><svg width="34" height="30" viewBox="0 0 34 30" fill="none" stroke="#fff" stroke-width="2"><rect x="2" y="2" width="30" height="26" rx="2"/><path d="M2 8h30M7 13h9v9H7zM20 14h8M20 18h8M20 22h8"/></svg></div>
    <div><h3>Step&nbsp; 03 &nbsp;-&nbsp;&nbsp; Lorem ipsum dolor sit amet</h3><p>Sed ut perspiciatis unde omnis iste natus error sit voluptatem accusantium doloremque</p></div>
  </div>

  <a class="abs btn btn-quote">Get a free quote
    <svg width="14" height="14" viewBox="0 0 14 14"><circle cx="7" cy="7" r="7" fill="#fff"/><path d="M5 4l3.5 3L5 10" stroke="#b49fd2" stroke-width="2" fill="none"/></svg></a>
</section>

<section>
  <h2 class="abs heading works-title">Our Works</h2>
  <div class="abs works">
    <div role="img" aria-label="Photo of a modern kitchen interior" style="background:linear-gradient(135deg,#e8e4df,#3b3936)"></div>
    <div role="img" aria-label="Photo of a Tudor style house" style="background:linear-gradient(180deg,#e4e4e2 40%,#6a4a36 70%,#5f7a40)"></div>
    <div role="img" aria-label="Photo of a large white farmhouse" style="background:linear-gradient(180deg,#d8e0e8 30%,#bfc4cc 55%,#7fa446)"></div>
    <div role="img" aria-label="Photo of a desktop monitor showing a website on a wooden desk" style="background:linear-gradient(160deg,#2d2f33 35%,#f2f2f0 50%,#c99a62)"></div>
    <div role="img" aria-label="Photo of a man typing on a laptop" style="background:linear-gradient(135deg,#f0ece4,#7d8fa3 60%,#4b4a48)"></div>
    <div role="img" aria-label="Photo of a man working on a laptop in a kitchen" style="background:linear-gradient(135deg,#ece8e2,#6d86a3 60%,#3a3a3a)"></div>
    <div role="img" aria-label="Photo of a modern kitchen interior" style="background:linear-gradient(135deg,#e8e4df,#3b3936)"></div>
    <div role="img" aria-label="Photo of two colleagues reviewing work on a laptop" style="background:linear-gradient(135deg,#1f3a4e,#c8442e 45%,#b8b6b2)"></div>
  </div>
</section>

<section>
  <div class="abs clients" role="img" aria-label="Faded photo of a house behind a purple overlay"></div>
  <h2 class="abs heading clients-title">What our clients say</h2>

  <article class="abs card" style="left:112px">
    <svg class="abs card-flag" width="44" height="44" viewBox="0 0 44 44"><path d="M0 0h44L0 44z" fill="#00a990"/><text x="5" y="20" fill="#fff" font-family="Georgia,serif" font-size="20" font-weight="700">“</text></svg>
    <blockquote>Sed ut perspiciatis unde omnis iste natus error sit voluptatemdoloremquelaudantium, totam rem aperiam, eaque ipsa</blockquote>
    <div class="stars">★★★★★</div>
    <div class="avatar" role="img" aria-label="Client portrait"></div>
    <div class="person"><strong>Dana Morrow</strong><span>Businessman</span></div>
  </article>
  <article class="abs card" style="left:441px">
    <svg class="abs card-flag" width="44" height="44" viewBox="0 0 44 44"><path d="M0 0h44L0 44z" fill="#00a990"/><text x="5" y="20" fill="#fff" font-family="Georgia,serif" font-size="20" font-weight="700">“</text></svg>
    <blockquote>Sed ut perspiciatis unde omnis iste natus error sit voluptatemdoloremquelaudantium, totam rem aperiam, eaque ipsa</blockquote>
    <div class="stars">★★★★★</div>
    <div class="avatar" role="img" aria-label="Client portrait"></div>
    <div class="person"><strong>Dana Morrow</strong><span>Businessman</span></div>
  </article>
  <article class="abs card" style="left:769px">
    <svg class="abs card-flag" width="44" height="44" viewBox="0 0 44 44"><path d="M0 0h44L0 44z" fill="#00a990"/><text x="5" y="20" fill="#fff" font-family="Georgia,serif" font-size="20" font-weight="700">“</text></svg>
    <blockquote>Sed ut perspiciatis unde omnis iste natus error sit voluptatemdoloremquelaudantium, totam rem aperiam, eaque ipsa</blockquote>
    <div class="stars">★★★★★</div>
    <div class="avatar" role="img" aria-label="Client portrait" style="background:linear-gradient(135deg,#f2f2f2,#c9b9a8)"></div>
    <div class="person"><strong>Dana Morrow</strong><span>Businessman</span></div>
  </article>
</section>

<section>
  <div class="abs contact"></div>
  <h2 class="abs heading contact-title">Contact Us</h2>
  <p class="abs contact-lead">At vero eos et accusamus et iusto odio dignissimos ducimus qui blanditiis praesentium voluptatum deleniti atque corrupti quos dolores et quas molestias excepturi sint occaecati cupiditate</p>

  <div class="abs info" style="top:2533px">
    <div class="info-icon"><svg width="24" height="26" viewBox="0 0 24 26" fill="none" stroke="#fabb94" stroke-width="1.6"><path d="M12 24s8-8 8-14a8 8 0 0 0-16 0c0 6 8 14 8 14z"/><circle cx="12" cy="10" r="3"/></svg></div>
    <div><h4>Location</h4><p>18 Linden Row, Ashbury MA<br>01100</p></div>
  </div>
  <div class="abs info" style="top:2631px">
    <div class="info-icon"><svg width="26" height="22" viewBox="0 0 26 22" fill="none" stroke="#fabb94" stroke-width="1.6"><rect x="2" y="5" width="22" height="15"/><path d="M2 5l11 9 11-9M6 2h14v7"/></svg></div>
    <div><h4>Email Us</h4><p>hello@quintarelweb.com</p></div>
  </div>
  <div class="abs info" style="top:2706px">
    <div class="info-icon"><svg width="24" height="24" viewBox="0 0 24 24" fill="none" stroke="#fabb94" stroke-width="1.6"><path d="M5 3l4 1 1 5-2 2a12 12 0 0 0 5 5l2-2 5 1 1 4c-1 2-3 3-5 2C9 19 5 15 3 8 2 6 3 4 5 3z"/></svg></div>
    <div><h4>Contact Us</h4><p class="big">1-555-014-2287</p></div>
  </div>

  <div class="abs field" style="top:2520px">First Name <svg width="14" height="14" viewBox="0 0 14 14" fill="none" stroke="#555" stroke-width="1.3"><circle cx="7" cy="7" r="6"/><circle cx="7" cy="5.5" r="2"/><path d="M3 11c2-3 6-3 8 0"/></svg></div>
  <div class="abs field" style="top:2580px">Email <svg width="14" height="11" viewBox="0 0 14 11" fill="none" stroke="#555" stroke-width="1.3"><rect x="1" y="1" width="12" height="9"/><path d="M1 1l6 5 6-5"/></svg></div>
  <div class="abs field" style="top:2640px">Phone No <svg width="12" height="12" viewBox="0 0 24 24" fill="#555"><path d="M5 2l5 1 1 6-3 2a13 13 0 0 0 5 5l2-3 6 1 1 5c-1 2-3 3-5 3C9 21 3 15 2 7c0-2 1-4 3-5z"/></svg></div>
  <div class="abs field" style="top:2700px">Post Code <svg width="10" height="13" viewBox="0 0 10 13" fill="#555"><path d="M5 13S0 7 0 5a5 5 0 0 1 10 0c0 2-5 8-5 8z"/><circle cx="5" cy="5" r="2" fill="#fff"/></svg></div>
  <div class="abs field field-message">Message <svg width="15" height="13" viewBox="0 0 15 13" fill="none" stroke="#555" stroke-width="1.3"><path d="M2 2h11v7H6l-3 3V9H2z"/></svg></div>
  <a class="abs btn btn-send">Get a quote
    <svg width="14" height="14" viewBox="0 0 14 14"><circle cx="7" cy="7" r="7" fill="#fff"/><path d="M5 4l3.5 3L5 10" stroke="#b49fd2" stroke-width="2" fill="none"/></svg></a>
</section>

<footer class="abs footer">© 2021 Brelvox Studio. All Rights Reserved</footer>

</body>
</html>
```